Website for Torvel Capital - investment banking firm

We have a corporate identity (thanks to Ravinka/31842) and want to extend that into a website design.  See the attached zipped files.
We have software folks in-house to do the coding.
See the attached Project Brief & Notes for more details.  Don't worry about the actual text - lorem ipsum will be fine.
The server will be Apache.
Thank you!
Desmond

Industry/Entity Type
Investment

```html
<!DOCTYPE html>
<html lang="en">
<head>
<meta charset="utf-8">
<title>Torvel Capital</title>
<link rel="stylesheet" href="https://fonts.googleapis.com/css2?family=Cinzel:wght@400;600&family=Libre+Baskerville&family=Mulish:ital,wght@0,400;0,600;0,800;1,400&display=swap">
<style>
  :root {
    --brand-blue: #0a5aa8;
    --nav-blue: #0b5aab;
    --nav-link: #8fb8e6;
    --deep-blue: #003a78;
    --mid-blue: #0066c8;
    --light-blue: #4a95dc;
    --heading-grey: #4e5a72;
    --text-grey: #56637a;
    --quote-bg: #f0f3f6;
    --quote-border: #c9d0da;
    --footer-bg: #dfe4ef;
    --footer-text: #5b6785;
    --bar-blue: #0b4d9c;
    --page-bg: #f8fafc;
    --white: #ffffff;
  }
  * { margin: 0; padding: 0; box-sizing: border-box; }
  html, body { width: 1024px; height: 1200px; overflow: hidden; }
  body {
    position: relative;
    background: var(--page-bg);
    font-family: "Mulish", Arial, sans-serif;
    color: var(--text-grey);
  }
  .abs { position: absolute; }

  /* Header */
  .site-header { left: 0; top: 0; width: 1024px; height: 70px; background: var(--white); }
  .brand { left: 138px; top: 20px; display: flex; align-items: center; gap: 10px; }
  .brand-mark { width: 28px; height: 28px; background: var(--brand-blue); }
  .brand-name { font-family: "Cinzel", serif; font-weight: 600; font-size: 24px; color: var(--brand-blue); letter-spacing: 0.5px; }

  .main-nav { left: 0; top: 70px; width: 1024px; height: 46px; background: var(--nav-blue); box-shadow: 0 2px 4px rgba(0,0,0,.15); }
  .main-nav ul { list-style: none; display: flex; position: absolute; left: 154px; top: 0; height: 46px; align-items: center; gap: 30px; }
  .main-nav a { font-weight: 800; font-size: 12.6px; color: var(--nav-link); text-decoration: none; }
  .main-nav a.active { color: var(--white); }

  /* Side areas */
  .side-pattern { top: 150px; width: 128px; height: 250px; background: radial-gradient(ellipse at center, #c6d6ea 0%, rgba(198,214,234,0) 70%); }
  .slider-arrow { top: 246px; width: 44px; height: 47px; background: #b9bcc2; display: flex; align-items: center; justify-content: center; }

  /* Hero */
  .hero { left: 128px; top: 116px; width: 768px; height: 339px; background: linear-gradient(100deg, #4b5c78 0%, #8aa3c6 35%, #cdd9ea 60%, #eef2f8 80%, #c8d6ea 100%); }
  .hero-title { left: 522px; top: 184px; font-family: "Cinzel", serif; font-size: 37px; line-height: 46px; color: var(--brand-blue); }
  .hero-text { left: 524px; top: 338px; width: 300px; font-size: 13.5px; line-height: 19px; color: #4a5466; }

  /* Feature panels */
  .panel { top: 455px; width: 256px; height: 239px; color: var(--white); }
  .panel-who { left: 128px; background: linear-gradient(180deg, #0058ad 0%, #003a78 100%); }
  .panel-services { left: 384px; background: linear-gradient(180deg, #0068cc 0%, #004a98 100%); }
  .panel-clients { left: 640px; background: linear-gradient(180deg, #4b97dc 0%, #2f72b6 100%); }
  .panel h2 { position: absolute; top: 28px; font-family: "Libre Baskerville", serif; font-weight: 400; font-size: 18px; }
  .panel p { position: absolute; top: 76px; font-size: 10px; line-height: 14.4px; }
  .panel-who h2, .panel-who p { left: 26px; width: 210px; }
  .panel-services h2 { left: 23px; }
  .panel-clients h2, .panel-clients p { left: 24px; width: 210px; }
  .services-label { position: absolute; left: 23px; top: 76px; font-size: 10px; font-weight: 800; }
  .services-list { position: absolute; left: 23px; top: 96px; list-style: none; font-size: 10px; }
  .services-list li { height: 20px; display: flex; align-items: flex-start; gap: 5px; }
  .services-list svg { margin-top: 3px; }
  .btn { position: absolute; top: 187px; width: 64px; height: 27px; border-radius: 14px; background: linear-gradient(#ffffff, #e6e8ec); border: 1px solid #c9ced6; font-size: 9px; color: #69707d; display: flex; align-items: center; justify-content: center; }
  .panel-who .btn { left: 33px; }
  .panel-services .btn { left: 33px; }
  .panel-clients .btn { left: 34px; }

  /* Testimonial and about */
  .section-title { font-family: "Libre Baskerville", serif; font-weight: 400; font-size: 20px; color: var(--heading-grey); }
  .testimonial-title { left: 142px; top: 748px; }
  .avatar { left: 148px; top: 788px; width: 64px; height: 64px; border-radius: 50%; background: linear-gradient(160deg, #e8c39a, #c9906e); }
  .author-name { left: 130px; top: 868px; width: 100px; text-align: center; font-weight: 800; font-size: 12px; color: #7a8496; }
  .author-role { left: 120px; top: 886px; width: 120px; text-align: center; font-size: 10px; color: #7a8496; }
  .quote { left: 242px; top: 786px; width: 392px; height: 112px; background: var(--quote-bg); border: 1px solid var(--quote-border); }
  .quote-tail { left: 234px; top: 811px; }
  .quote p { position: absolute; left: 23px; top: 16px; width: 350px; font-style: italic; font-size: 12.8px; line-height: 19.2px; color: #6e7787; }
  .about-title { left: 650px; top: 748px; }
  .about-text { left: 651px; top: 786px; width: 240px; font-size: 10px; line-height: 14.4px; color: var(--text-grey); }
  .about-btn { left: 648px; top: 874px; }

  /* Footer */
  .site-footer { left: 0; top: 970px; width: 1024px; height: 196px; background: var(--footer-bg); }
  .footer-mark { left: 138px; top: 1008px; width: 92px; height: 92px; background: #c5d3e6; }
  .footer-heading { font-weight: 800; font-size: 10.4px; letter-spacing: .5px; color: var(--footer-text); }
  .footer-links { list-style: none; font-size: 8.8px; color: var(--footer-text); }
  .footer-links li { height: 19.2px; display: flex; align-items: center; gap: 4px; }
  .contact-item { left: 467px; display: flex; gap: 9px; font-size: 10px; line-height: 16px; color: var(--footer-text); }
  .contact-item svg { flex: none; margin-top: 1px; }
  .map { left: 650px; top: 1005px; width: 238px; height: 113px; background: linear-gradient(135deg, #e9e7df, #d8d6cd 55%, #b9c7d9); }

  .bottom-bar { left: 0; top: 1166px; width: 1024px; height: 34px; background: var(--bar-blue); font-size: 10px; color: #a9c2e6; }
  .bottom-bar span { position: absolute; top: 11px; }
</style>
</head>
<body>

<header class="site-header abs">
  <div class="brand abs">
    <span class="brand-mark"></span>
    <span class="brand-name">Torvel Capital</span>
  </div>
</header>

<nav class="main-nav abs">
  <ul>
    <li><a class="active" href="#">HOME</a></li>
    <li><a href="#">HISTORY</a></li>
    <li><a href="#">CLIENTS</a></li>
    <li><a href="#">OUR TEAM</a></li>
    <li><a href="#">COMPLETED DEALS</a></li>
    <li><a href="#">CURRENT SEARCHES</a></li>
    <li><a href="#">CONTACT US</a></li>
  </ul>
</nav>

<div class="side-pattern abs" style="left:0" role="img" aria-label="Dotted world map decoration"></div>
<div class="side-pattern abs" style="left:896px" role="img" aria-label="Dotted world map decoration"></div>

<div class="slider-arrow abs" style="left:0">
  <svg width="10" height="16" viewBox="0 0 10 16"><path d="M8 2 L2 8 L8 14" fill="none" stroke="#fff" stroke-width="2"/></svg>
</div>
<div class="slider-arrow abs" style="left:980px">
  <svg width="10" height="16" viewBox="0 0 10 16"><path d="M2 2 L8 8 L2 14" fill="none" stroke="#fff" stroke-width="2"/></svg>
</div>

<section class="hero abs" role="img" aria-label="Photo of a businessman in a suit in front of a glass office building"></section>
<h1 class="hero-title abs">Global,<br>Professional,<br>Trusted.</h1>
<p class="hero-text abs">Torvel Capital is an independent investment bank working for buyers in a number of industries.</p>

<section class="panel panel-who abs">
  <h2>Who We Are</h2>
  <p>Torvel Capital is an independent investment bank working for buyers in a number of industries. We utilize exceptional technology in finding companies to meet our client's search criteria. We will not waste a buyer's time, a seller's time, or our own time.</p>
  <span class="btn">Read More</span>
</section>

<section class="panel panel-services abs">
  <h2>Our Services</h2>
  <span class="services-label">OUR SERVICES INCLUDE::</span>
  <ul class="services-list">
    <li><svg width="4" height="7"><path d="M0 0 L4 3.5 L0 7Z" fill="#fff"/></svg>Buy-Side Acquisitions</li>
    <li><svg width="4" height="7"><path d="M0 0 L4 3.5 L0 7Z" fill="#fff"/></svg>Recapitalizations &amp; Growth Capital Partnerships</li>
    <li><svg width="4" height="7"><path d="M0 0 L4 3.5 L0 7Z" fill="#fff"/></svg>Sell-Side Transactions</li>
  </ul>
  <span class="btn">Read More</span>
</section>

<section class="panel panel-clients abs">
  <h2>Our Clients</h2>
  <p>Torvel Capital has a diverse array of clients ranging from multi-billion dollar strategic acquirers to large private equity funds. We will not engage a client as a buyer if we believe there is any chance of them wasting our time or a prospective seller's time.</p>
  <span class="btn">Read More</span>
</section>

<h2 class="section-title testimonial-title abs">Client Testimonial</h2>
<div class="avatar abs" role="img" aria-label="Portrait photo of the client"></div>
<div class="author-name abs">Marla Quen</div>
<div class="author-role abs">Managing Director</div>
<svg class="quote-tail abs" width="10" height="20" viewBox="0 0 10 20"><path d="M10 0 L1 10 L10 20" fill="#f0f3f6" stroke="#c9d0da"/></svg>
<blockquote class="quote abs">
  <p>“Vestibulum blandit faucibus urna in hendrerit. Vivamus leo dui, bibendum vitae hendrerit ac, volutpat quis dolor. Maecenas id lacinia odio, et malesuada lectus. Nulla et ante non metus consectetur vestibulum sed quis dolor.”</p>
</blockquote>

<h2 class="section-title about-title abs">About Torvel Capital</h2>
<p class="about-text abs">Torvel Capital's history in mergers and acquisitions traces back to 1998. We pride our selves in successfully matching buyers with sellers and enabling shareholders of all stakeholders in a transaction to prosper.</p>
<span class="btn about-btn">Read More</span>

<footer class="site-footer abs"></footer>
<div class="footer-mark abs"></div>

<div class="footer-heading abs" style="left:265px;top:1004px">NAVIGATION</div>
<ul class="footer-links abs" style="left:264px;top:1029px">
  <li><svg width="3" height="6"><path d="M0 0 L3 3 L0 6Z" fill="#5b6785"/></svg>HOME</li>
  <li><svg width="3" height="6"><path d="M0 0 L3 3 L0 6Z" fill="#5b6785"/></svg>HISTORY</li>
  <li><svg width="3" height="6"><path d="M0 0 L3 3 L0 6Z" fill="#5b6785"/></svg>CLIENTS</li>
  <li><svg width="3" height="6"><path d="M0 0 L3 3 L0 6Z" fill="#5b6785"/></svg>OUR TEAM</li>
</ul>
<ul class="footer-links abs" style="left:345px;top:1029px">
  <li><svg width="3" height="6"><path d="M0 0 L3 3 L0 6Z" fill="#5b6785"/></svg>COMPLETED DEALS</li>
  <li><svg width="3" height="6"><path d="M0 0 L3 3 L0 6Z" fill="#5b6785"/></svg>CURRENT SEARCHES</li>
  <li><svg width="3" height="6"><path d="M0 0 L3 3 L0 6Z" fill="#5b6785"/></svg>CONTACT US</li>
</ul>

<div class="footer-heading abs" style="left:458px;top:1002px">CONTACT DETAILS</div>
<div class="contact-item abs" style="top:1029px">
  <svg width="14" height="14" viewBox="0 0 14 14"><path d="M3 1 L5 4 L4 5.5 C5 8 6 9 8.5 10 L10 9 L13 11 L12 13 C6 13 1 8 1 2Z" fill="#5b6785"/></svg>
  <span>+1800-555-0142</span>
</div>
<div class="contact-item abs" style="top:1053px">
  <svg width="14" height="14" viewBox="0 0 14 14"><rect x="1" y="3" width="12" height="9" fill="none" stroke="#5b6785" stroke-width="1.3"/><path d="M1 3 L7 8 L13 3" fill="none" stroke="#5b6785" stroke-width="1.3"/></svg>
  <span>info@torvelcapital.example</span>
</div>
<div class="contact-item abs" style="top:1077px">
  <svg width="14" height="16" viewBox="0 0 14 16"><path d="M7 1 C3.5 1 2 3.5 2 5.5 C2 9 7 15 7 15 C7 15 12 9 12 5.5 C12 3.5 10.5 1 7 1Z" fill="#5b6785"/><circle cx="7" cy="5.5" r="2" fill="#dfe4ef"/></svg>
  <span>Your Address, Your Country<br>Your Zip Code</span>
</div>

<div class="map abs" role="img" aria-label="Street map showing the office location"></div>

<div class="bottom-bar abs">
  <span style="left:132px">Copyright © 2014 - TorvelCapital. All Rights reserved</span>
  <span style="left:779px">Privacy Policy</span>
  <span style="left:876px">Sitemap</span>
</div>

</body>
</html>
```